Velmora Consulting Business

** Please add the content information from my old business card
1. I would like to see a two sided business card with both options with the 1st Option--Tallow Spire-new WHITE BACKGROUND LOGO
2 nd Option-Tallow Spire - new BLACK- Background Logo
3rd -Option a business card with my Photo on the card
Please add the new word to the card information:
EXECUTION
AS THE OWNER'S REP
WE AIM TO ACHIEVE YOUR
INFRASTRUCTURE VISION with
OUR SPECIALIZATION & EXECUTION in:

FUNDING Planning
BUSINESS Planning
INFRASTRUCTURE Planning
PROJECT Management
Since 2012
_____________________________________________________________________
I want to get spot uv raised printing. I was liking a a nice rich white linen paper stock with black writing & NOT A COLORED CARD other than a variety of white or black cards concept

```html
<!DOCTYPE html>
<html lang="en">
<head>
<meta charset="utf-8">
<title>Velmora Consulting – Business Card</title>
<link href="https://fonts.googleapis.com/css2?family=Open+Sans:wght@400;600;700&display=swap" rel="stylesheet">
<style>
  :root {
    --stage: #161616;
    --ink: #231f20;
    --paper: #ffffff;
    --accent: #e5173f;
    --light-text: #f2f2f2;
  }
  * { margin: 0; padding: 0; box-sizing: border-box; }
  html, body { width: 1200px; height: 1015px; overflow: hidden; background: var(--stage); }
  body { position: relative; font-family: "Open Sans", Arial, sans-serif; }

  .card {
    position: absolute;
    left: 250px;
    width: 700px;
    height: 400px;
    background: var(--paper);
    overflow: hidden;
  }
  .card--back { top: 70px; }
  .card--front { top: 545px; }
  .card__shapes { position: absolute; inset: 0; }

  .brand {
    position: absolute;
    text-align: center;
    color: var(--ink);
  }
  .brand__name {
    font-weight: 700;
    font-size: 56px;
    line-height: 1;
    letter-spacing: -1px;
  }
  .brand__tag {
    font-weight: 400;
    font-size: 14px;
    letter-spacing: 11px;
    margin-top: 10px;
    padding-left: 11px;
  }
  .card--back .brand { left: 440px; width: 250px; top: 160px; }
  .card--front .brand { left: 20px; width: 290px; top: 160px; }

  .pitch {
    position: absolute;
    left: 42px;
    top: 78px;
    color: var(--light-text);
    font-size: 14.5px;
    line-height: 1.3;
  }
  .pitch__intro { margin-bottom: 20px; }
  .services { list-style: none; }
  .services li { position: relative; padding-left: 22px; }
  .services li::before {
    content: "";
    position: absolute;
    left: 2px; top: 7px;
    width: 8px; height: 8px;
    background: var(--accent);
  }
  .since { margin-top: 6px; padding-left: 22px; }

  .contact {
    position: absolute;
    left: 405px;
    top: 95px;
    color: var(--light-text);
  }
  .contact__name { font-weight: 700; font-size: 21px; line-height: 1.2; }
  .contact__role { color: var(--accent); font-size: 13px; letter-spacing: 0.3px; margin-bottom: 22px; }
  .contact__list { list-style: none; font-size: 14.5px; line-height: 1.6; }
  .contact__list li { display: flex; align-items: center; gap: 10px; }
  .contact__list svg { width: 14px; height: 14px; flex: none; }
  .contact__area { margin-top: 24px; font-size: 14.5px; padding-left: 24px; }
</style>
</head>
<body>

<section class="card card--back" aria-label="Card back">
  <svg class="card__shapes" viewBox="0 0 700 400" preserveAspectRatio="none">
    <polygon points="0,0 380,0 470,400 0,400" fill="var(--ink)"/>
    <line x1="380" y1="0" x2="470" y2="400" stroke="var(--accent)" stroke-width="3"/>
  </svg>
  <div class="pitch">
    <p class="pitch__intro">EXECUTION<br>AS THE OWNER'S REP<br>WE AIM TO ACHIEVE YOUR<br>INFRASTRUCTURE VISION with<br>OUR SPECIALIZATION &amp; EXECUTION in:</p>
    <ul class="services">
      <li>FUNDING Planning</li>
      <li>BUSINESS Planning</li>
      <li>INFRASTRUCTURE Planning</li>
      <li>PROJECT Management</li>
    </ul>
    <p class="since">Since 2012</p>
  </div>
  <div class="brand">
    <div class="brand__name">Velmora</div>
    <div class="brand__tag">CONSULTING</div>
  </div>
</section>

<section class="card card--front" aria-label="Card front">
  <svg class="card__shapes" viewBox="0 0 700 400" preserveAspectRatio="none">
    <polygon points="290,0 700,0 700,400 380,400" fill="var(--ink)"/>
    <line x1="290" y1="0" x2="380" y2="400" stroke="var(--accent)" stroke-width="3"/>
  </svg>
  <div class="brand">
    <div class="brand__name">Velmora</div>
    <div class="brand__tag">CONSULTING</div>
  </div>
  <div class="contact">
    <p class="contact__name">Renata Holloway-Brisk</p>
    <p class="contact__role">CEO / LEAD PROJECT MANAGER</p>
    <ul class="contact__list">
      <li>
        <svg viewBox="0 0 24 24" aria-hidden="true"><path fill="var(--accent)" d="M6.6 10.8a15.1 15.1 0 0 0 6.6 6.6l2.2-2.2a1 1 0 0 1 1-.25 11.4 11.4 0 0 0 3.6.57 1 1 0 0 1 1 1V20a1 1 0 0 1-1 1A17 17 0 0 1 3 4a1 1 0 0 1 1-1h3.5a1 1 0 0 1 1 1c0 1.25.2 2.45.57 3.6a1 1 0 0 1-.25 1z"/></svg>
        867 555.0192
      </li>
      <li>
        <svg viewBox="0 0 24 24" aria-hidden="true"><path fill="var(--accent)" d="M2 5h20v14H2z M3 6l9 7 9-7" stroke="var(--ink)" stroke-width="1.5"/></svg>
        renata@velmora.ca
      </li>
      <li>
        <svg viewBox="0 0 24 24" aria-hidden="true"><g fill="none" stroke="var(--accent)" stroke-width="2"><circle cx="12" cy="12" r="9"/><path d="M3 12h18M12 3c3 3 3 15 0 18M12 3c-3 3-3 15 0 18"/></g></svg>
        www.velmora.ca
      </li>
    </ul>
    <p class="contact__area">Harrowvale NT • Elmbrook NB</p>
  </div>
</section>

</body>
</html>
```